TALMORK

The business want a professional looking business card. We have a scetch we will add but want the extra upgrade, and would like more suggestions for variations of our business cards.

```html
<!DOCTYPE html>
<html lang="en">
<head>
<meta charset="utf-8">
<title>TALMORK business card</title>
<link rel="stylesheet" href="https://fonts.googleapis.com/css2?family=Cinzel:wght@500&family=Montserrat:wght@400;700&display=swap">
<style>
  :root {
    --stage: #1c1c1d;
    --card: #19191a;
    --card-panel: #222224;
    --gold: #c9a04a;
    --gold-light: #ecc877;
    --gold-dark: #7d5a1c;
    --ink-light: #f2f2f2;
    --emboss: #2d2d2f;
  }
  * { box-sizing: border-box; margin: 0; padding: 0; }
  html, body { width: 1200px; height: 801px; overflow: hidden; }
  body {
    background: var(--stage);
    position: relative;
    font-family: "Montserrat", sans-serif;
  }
  .card {
    position: absolute;
    top: 250px;
    width: 520px;
    height: 300px;
    border-radius: 18px;
    background: var(--card);
    overflow: hidden;
  }
  .card--front { left: 50px; }
  .card--back { left: 630px; }

  .card__sweep { position: absolute; inset: 0; width: 100%; height: 100%; }

  .brand {
    position: absolute;
    font-family: "Cinzel", serif;
    font-weight: 500;
    letter-spacing: 0.12em;
  }
  .card--front .brand {
    left: 40px; top: 42px;
    font-size: 34px;
    color: var(--gold);
  }
  .identity {
    position: absolute;
    left: 56px; top: 116px;
  }
  .identity__marker {
    position: absolute;
    left: -56px; top: 6px;
    width: 18px; height: 26px;
    background: var(--gold-dark);
  }
  .identity__name {
    font-weight: 700;
    font-size: 17px;
    color: var(--gold);
  }
  .identity__role {
    font-size: 13px;
    color: var(--ink-light);
    margin-top: 3px;
  }
  .contacts {
    position: absolute;
    left: 56px; top: 186px;
    list-style: none;
  }
  .contacts__item {
    display: flex;
    align-items: center;
    gap: 10px;
    font-size: 12.5px;
    color: var(--ink-light);
    margin-bottom: 9px;
  }
  .contacts__icon { width: 13px; height: 13px; flex: none; }

  .panel-mark {
    position: absolute;
    right: 40px; top: 40px;
    display: flex; align-items: center; gap: 10px;
    font-family: "Montserrat", sans-serif;
    font-weight: 700;
    font-size: 22px;
    letter-spacing: 0.08em;
    color: var(--emboss);
  }
  .panel-mark__dot { width: 14px; height: 14px; border-radius: 50%; background: var(--emboss); }

  .card--back .brand {
    left: 0; right: 0; top: 124px;
    text-align: center;
    font-size: 40px;
    color: var(--emboss);
  }
</style>
</head>
<body>
  <section class="card card--front" aria-label="Card front">
    <svg class="card__sweep" viewBox="0 0 520 300" aria-hidden="true">
      <defs>
        <linearGradient id="gold-band" x1="0" y1="1" x2="1" y2="0">
          <stop offset="0" stop-color="#7d5a1c"/>
          <stop offset="0.55" stop-color="#ecc877"/>
          <stop offset="1" stop-color="#8a6420"/>
        </linearGradient>
      </defs>
      <path d="M520 110 Q430 220 300 300 L520 300 Z" fill="#222224"/>
      <path d="M520 96 Q425 215 286 300 L304 300 Q432 222 520 118 Z" fill="url(#gold-band)"/>
      <path d="M520 126 Q438 228 314 300 L320 300 Q442 232 520 130 Z" fill="#8a6420"/>
    </svg>

    <div class="brand">TALMORK</div>

    <div class="panel-mark"><span class="panel-mark__dot"></span>TALMORK</div>

    <div class="identity">
      <span class="identity__marker"></span>
      <p class="identity__name">Anders Holm Rasmussen</p>
      <p class="identity__role">CEO &amp; Founder</p>
    </div>

    <ul class="contacts">
      <li class="contacts__item">
        <svg class="contacts__icon" viewBox="0 0 16 16" aria-hidden="true"><path fill="#c9a04a" d="M3 1l3 3-1.5 2a9 9 0 0 0 5.5 5.5L12 10l3 3-2 2C7 15 1 9 1 3z"/></svg>
        004791234567
      </li>
      <li class="contacts__item">
        <svg class="contacts__icon" viewBox="0 0 16 16" aria-hidden="true"><rect x="1" y="3" width="14" height="10" fill="#c9a04a"/><path d="M1 3l7 6 7-6" fill="none" stroke="#19191a" stroke-width="1.4"/></svg>
        talmork.llc@mailbox.com
      </li>
      <li class="contacts__item">
        <svg class="contacts__icon" viewBox="0 0 16 16" aria-hidden="true"><circle cx="8" cy="8" r="7" fill="#c9a04a"/><path d="M1 8h14M8 1c-3 4-3 10 0 14M8 1c3 4 3 10 0 14" fill="none" stroke="#19191a" stroke-width="1"/></svg>
        www.talmork.llc
      </li>
    </ul>
  </section>

  <section class="card card--back" aria-label="Card back">
    <div class="brand">TALMORK</div>
  </section>
</body>
</html>
```